Business Card Design

We like to use greens as you will see in our logo (but not TOO much green). We are a Dental Clinic in a somewhat eccentric community. We do not like the dated sharp designs which we see many dentists use. We're looking for something bright and fresh while still maintaining the integrity of the profession. Elegance is not necessarily what we are going for... we need for the design to be "mature" but also up-lifting.

See our logo.
Updates

Project Deadline Extended
Reason: We have 5 designs which we like. But we'd like to see a few more before committing to a design.

Project Deadline Extended
Reason: We are awaiting revisions to this project. We are still welcoming designs while we wait to see if designers are able to provide to us the revisions we require in order to proceed with a selection.

Target Market(s)

Younger families - ages late 20's to early 40's

Industry/Entity Type

Business

Contact Information for Business Card

Corwel T. Banfry DDS 2730 W. Halvert Rd. Ste. 7 Royal Oak, MI 48391 (248)555-0174 FX (248)555-0189 info@BrightwellDentalCareMi.com BrigthwellDentalCareMi.com on the back of the card we need an appointment reminder (For____ Date___ Time____) with "If you are unable to keep your appointment, kindly give 48 hours notice" at the bottom. No use of teeth in the design. DOUBLE SIDED DESIGN

Requirements
Should not have
• The use of pictures of teeth

```html
<!DOCTYPE html>
<html lang="en">
<head>
<meta charset="utf-8">
<title>Brightwell Dental Care — Business Card</title>
<link rel="stylesheet" href="https://fonts.googleapis.com/css2?family=Source+Sans+3:ital,wght@0,400;0,600;0,700;1,400&family=Cinzel:wght@600&display=swap">
<style>
  :root {
    --green-dark: #166b38;
    --green-mid: #2e8b3e;
    --green-light: #7ccb2b;
    --ink: #333333;
    --paper: #ffffff;
    --backdrop: #eeeeec;
    --box-line: #4a4a4a;
  }
  * { margin: 0; padding: 0; box-sizing: border-box; }
  html, body { width: 1200px; height: 1182px; overflow: hidden; }
  body {
    background: var(--backdrop);
    font-family: "Source Sans 3", Arial, sans-serif;
    color: var(--ink);
    position: relative;
  }
  .card {
    position: absolute;
    width: 941px;
    height: 539px;
    background: var(--paper);
    overflow: hidden;
    box-shadow: 0 2px 6px rgba(0,0,0,0.18);
  }
  .card--front { left: 21px; top: 27px; }
  .card--back { left: 220px; top: 609px; }

  .brand-name {
    position: absolute;
    color: var(--green-dark);
    font-weight: 600;
    line-height: 1;
    text-align: center;
  }
  .card--front .brand-name { left: 60px; top: 170px; width: 430px; }
  .brand-name__main { display: block; font-size: 78px; letter-spacing: -1px; }
  .brand-name__sub { display: block; font-size: 40px; letter-spacing: 1px; margin-top: 8px; }
  .card--back .brand-name { left: 52px; top: 40px; width: 270px; }
  .card--back .brand-name__main { font-size: 50px; }
  .card--back .brand-name__sub { font-size: 26px; margin-top: 5px; }

  .divider {
    position: absolute;
    left: 529px; top: 85px;
    width: 2px; height: 278px;
    background: #b9b9b9;
  }
  .holder { position: absolute; left: 551px; top: 88px; }
  .holder__name { color: var(--green-dark); font-weight: 700; font-size: 35px; line-height: 1.1; }
  .holder__title { font-size: 27px; line-height: 1.2; }
  .contact-list { position: absolute; left: 551px; top: 196px; list-style: none; }
  .contact-list li {
    display: flex; align-items: center; gap: 6px;
    height: 41.5px; font-size: 24px;
  }
  .contact-list svg { width: 20px; height: 20px; fill: var(--green-dark); flex: none; }

  .wave { position: absolute; left: 0; top: 0; width: 941px; height: 539px; }
  .address {
    position: absolute; left: 0; bottom: 8px; width: 100%;
    text-align: center; color: var(--paper); font-size: 23px;
  }

  .appointment-title {
    position: absolute; left: 80px; top: 176px;
    font-family: "Cinzel", Georgia, serif;
    color: var(--green-dark);
    font-size: 33px; letter-spacing: 0.5px;
  }
  .field { position: absolute; font-size: 26px; display: flex; align-items: baseline; white-space: nowrap; }
  .field__line { display: inline-block; border-bottom: 2px dotted #777; height: 1px; margin: 0 8px; }
  .field--name { left: 83px; top: 252px; }
  .field--date { left: 83px; top: 321px; }
  .field--next { left: 83px; top: 386px; }
  .slot-box {
    display: inline-block; width: 170px; height: 37px;
    border: 2px solid var(--box-line); border-radius: 5px;
  }
  .slot-box--first { margin-left: 22px; }
  .slot-box--second { margin-left: 39px; }

  .weekdays { position: absolute; right: 28px; top: 0; list-style: none; }
  .weekdays li {
    position: absolute; right: 0;
    display: flex; align-items: center; gap: 10px;
    font-weight: 600; font-size: 27px; white-space: nowrap;
  }
  .weekdays .day-box {
    width: 59px; height: 34px;
    border: 2px solid var(--box-line); border-radius: 5px;
  }
  .notice {
    position: absolute; left: 77px; top: 462px;
    font-style: italic; font-size: 27px;
  }
  .back-band {
    position: absolute; left: 0; bottom: 0;
    width: 100%; height: 11px; background: var(--green-dark);
  }
</style>
</head>
<body>

<section class="card card--front" aria-label="Card front">
  <svg class="wave" viewBox="0 0 941 539" aria-hidden="true">
    <path d="M0 428 C 280 380 620 405 941 485 L941 506 C 620 440 290 418 0 458 Z" fill="var(--green-light)"/>
    <path d="M0 466 C 300 432 620 455 941 508 L941 539 L0 539 Z" fill="var(--green-dark)"/>
  </svg>

  <div class="brand-name">
    <span class="brand-name__main">Brightwell</span>
    <span class="brand-name__sub">DENTAL CARE</span>
  </div>

  <div class="divider"></div>

  <div class="holder">
    <p class="holder__name">Corwel T. Banfry</p>
    <p class="holder__title">DDS</p>
  </div>

  <ul class="contact-list">
    <li>
      <svg viewBox="0 0 20 20" aria-label="Phone"><path d="M5 2 L8 6 L6.5 8 C7.5 10 10 12.5 12 13.5 L14 12 L18 15 L16 18 C9 18 2 11 2 4 Z"/></svg>
      (248)555-0174
    </li>
    <li>
      <svg viewBox="0 0 20 20" aria-label="Fax"><path d="M5 2 H15 V7 H5 Z M2 8 H18 V15 H15 V18 H5 V15 H2 Z M7 13 V16 H13 V13 Z" fill-rule="evenodd"/></svg>
      (248)555-0189
    </li>
    <li>
      <svg viewBox="0 0 20 20" aria-label="Email"><path d="M2 5 H18 V16 H2 Z M3 6 L10 11 L17 6" /><path d="M3 6.5 L10 11.5 L17 6.5" stroke="#fff" stroke-width="1.4" fill="none"/></svg>
      info@BrightwellDentalCareMi.com
    </li>
    <li>
      <svg viewBox="0 0 20 20" aria-label="Website"><circle cx="10" cy="10" r="8"/><path d="M2 10 H18 M10 2 V18 M4 5.5 H16 M4 14.5 H16 M10 2 C6 6 6 14 10 18 M10 2 C14 6 14 14 10 18" stroke="#fff" stroke-width="1" fill="none"/></svg>
      BrigthwellDentalCareMi.com
    </li>
  </ul>

  <p class="address">2730 W. Halvert Rd. Ste. 7 Royal Oak, MI 48391</p>
</section>

<section class="card card--back" aria-label="Card back">
  <div class="brand-name">
    <span class="brand-name__main">Brightwell</span>
    <span class="brand-name__sub">DENTAL CARE</span>
  </div>

  <h2 class="appointment-title">YOUR APPOINTMENT</h2>

  <div class="field field--name">Name :<span class="field__line" style="width:520px"></span></div>
  <div class="field field--date">Date :<span class="field__line" style="width:170px;margin-left:22px"></span>Time :<span class="field__line" style="width:160px"></span>am / pm</div>
  <div class="field field--next">Next Appointment<span class="slot-box slot-box--first"></span><span class="slot-box slot-box--second"></span></div>

  <ul class="weekdays">
    <li style="top:80px">MON <span class="day-box"></span></li>
    <li style="top:145px">TUE <span class="day-box"></span></li>
    <li style="top:209px">WED <span class="day-box"></span></li>
    <li style="top:277px">THU <span class="day-box"></span></li>
    <li style="top:336px">FRI <span class="day-box"></span></li>
    <li style="top:391px">SAT <span class="day-box"></span></li>
  </ul>

  <p class="notice">If you are unable to keep your appointment, kindly give 48 hours notice</p>
  <div class="back-band"></div>
</section>

</body>
</html>
```